English and Spanish Language School Needs a Business Card

Need a business card design a startup company called Maribel Language School. The company will offer English and Spanish conversational level courses designed to make the learner feel comfortable with grammar and vocabulary. We would like to see a logo with some colour that should communicate learning, growth.

Target Market(s)

Consumers and businesses

Industry/Entity Type

Education

Contact Information for Business Card

TBD

Font styles to use
Serif

Requirements
Must have
• Include the following
• Logo
• Name
• Title
• Cellphone Number
• Office Phone number
• Email address
• Office Address

```html
<!DOCTYPE html>
<html lang="en">
<head>
<meta charset="utf-8">
<title>Maribel Language School – Business Card</title>
<link rel="stylesheet" href="https://fonts.googleapis.com/css2?family=Montserrat:wght@400;500;700;800&display=swap">
<style>
  :root {
    --brand-red: #c81f27;
    --brand-teal: #1fa3a8;
    --card-white: #ffffff;
    --backdrop: #2b2b2d;
  }
  * { margin: 0; padding: 0; box-sizing: border-box; }
  html, body {
    width: 1200px; height: 900px; overflow: hidden;
    background: var(--backdrop);
    font-family: "Montserrat", Arial, sans-serif;
  }
  .stage {
    position: relative; width: 1200px; height: 900px;
  }
  .card {
    position: absolute; left: 290px; width: 620px; height: 354px;
    border-radius: 22px; overflow: hidden;
  }
  .card--front { top: 76px; background: var(--brand-red); color: var(--card-white); }
  .card--back  { top: 470px; background: var(--card-white); }

  .front-brand {
    position: absolute; left: 0; right: 0; top: 118px; text-align: center;
  }
  .brand-name {
    font-weight: 800; line-height: 1; letter-spacing: -1px;
  }
  .front-brand .brand-name { font-size: 60px; color: var(--card-white); }
  .front-brand .brand-sub {
    font-weight: 500; font-size: 24px; color: var(--card-white); margin-top: 4px;
  }
  .front-web {
    position: absolute; left: 0; right: 0; bottom: 34px; text-align: center;
    font-size: 15px; font-weight: 500; letter-spacing: 0.3px;
  }

  .contact {
    position: absolute; left: 44px; top: 112px;
    color: var(--brand-teal); font-size: 16px; line-height: 1.3;
  }
  .contact-name { color: var(--brand-red); font-weight: 700; font-size: 24px; line-height: 1.2; }
  .contact-title { margin-bottom: 6px; }
  .contact-list { list-style: none; margin-top: 6px; }
  .contact-list li { display: flex; align-items: center; gap: 10px; height: 21px; }
  .contact-list svg { width: 13px; height: 13px; flex: none; }
  .contact-list .contact-web { color: var(--brand-red); font-weight: 700; }

  .back-brand {
    position: absolute; right: 40px; top: 168px; text-align: right;
  }
  .back-brand .brand-name { font-size: 40px; color: var(--brand-red); }
  .back-brand .brand-sub { font-size: 16px; font-weight: 500; color: var(--brand-red); margin-top: 2px; }
</style>
</head>
<body>
<main class="stage">
  <section class="card card--front" aria-label="Card front">
    <div class="front-brand">
      <div class="brand-name">Maribel</div>
      <div class="brand-sub">Language School</div>
    </div>
    <div class="front-web">www.maribellanguageschool.com</div>
  </section>

  <section class="card card--back" aria-label="Card back">
    <div class="contact">
      <div class="contact-name">Daniel Hartley</div>
      <div class="contact-title">Director</div>
      <div>PO Box 218</div>
      <div>Elmwood VIC 3902</div>
      <ul class="contact-list">
        <li>
          <svg viewBox="0 0 12 12" aria-hidden="true"><rect x="3" y="0.8" width="6" height="10.4" rx="1.2" fill="none" stroke="var(--brand-red)" stroke-width="1.4"/><circle cx="6" cy="9" r="0.8" fill="var(--brand-red)"/></svg>
          <span>+330 2471-9025</span>
        </li>
        <li>
          <svg viewBox="0 0 12 12" aria-hidden="true"><path d="M2.5 1.2 L4.6 1 L5.4 3.6 L4.1 4.6 Q5.2 7 7.4 7.9 L8.4 6.6 L11 7.4 L10.8 9.5 Q10.4 11 8.8 10.8 Q2 9.6 1.2 3.2 Q1 1.6 2.5 1.2 Z" fill="var(--brand-red)"/></svg>
          <span>+330 2483-1167</span>
        </li>
        <li>
          <svg viewBox="0 0 12 12" aria-hidden="true"><rect x="1" y="2.5" width="10" height="7" rx="0.8" fill="none" stroke="var(--brand-red)" stroke-width="1.3"/><path d="M1.4 3 L6 6.6 L10.6 3" fill="none" stroke="var(--brand-red)" stroke-width="1.3"/></svg>
          <span>hello@maribelschool.com</span>
        </li>
        <li>
          <svg viewBox="0 0 12 12" aria-hidden="true"><circle cx="6" cy="6" r="5" fill="var(--brand-red)"/><path d="M1 6 H11 M6 1 Q3 6 6 11 M6 1 Q9 6 6 11" fill="none" stroke="#fff" stroke-width="0.8"/></svg>
          <span class="contact-web">maribellanguageschool.com</span>
        </li>
      </ul>
    </div>
    <div class="back-brand">
      <div class="brand-name">Maribel</div>
      <div class="brand-sub">Language School</div>
    </div>
  </section>
</main>
</body>
</html>
```